Corvana Tongue Works, LLC

We need a business card that includes information about our business and conveys a reliable business that provides document translation services and interpreters for a variety of corporate and individual clients. We want to come across as professional, reliable, yet approachable. It should include the following on one side:

ESL / ENL Language Classes, Private Lessons, and Online Tutors
PLEXA Training and Testing
Translating & Interpreting Services
Contact us about Over-the-Phone Interpreting in over 200 languages
24/7/365
www.corvanatongue.example

The other side should include (555) 481-3062

Rhoda Pelling, President
482 Garnet Ave., Ste. 219
Indianapolis, IN 40917

Please add USA as part of the address. Also, please add rmpelling@corvanatongueworks.example as the e-mail address. Thank you.

Target Market(s)

Business professionals, their families, the international community

Industry/Entity Type

Business

Contact Information for Business Card

24/7/365
www.corvanatongue.example

(555) 481-3062

Rhoda Pelling, President
482 Garnet Ave., Ste. 219
Indianapolis, IN 40917
USA

Font styles to use
Sans Serif

Colors

Designer to choose colors to be used in the design.

Requirements
Must have
• See project description
• e-mail address and web address
• Phone number
Nice to have
• a globe
• physical address
Should not have
• Should not have the same color scheme as other agencies in our market in Indiana unless it is blue and black. No purple or yellow.

```html
<!DOCTYPE html>
<html lang="en">
<head>
<meta charset="utf-8">
<title>Corvana Tongue Works business card</title>
<link rel="stylesheet" href="https://fonts.googleapis.com/css2?family=Roboto:wght@400;500&family=Oxygen:wght@400&display=swap">
<style>
  :root {
    --bg: #d9d7d4;
    --ink: #111213;
    --paper: #ffffff;
    --blue: #2394d6;
    --card-black: #050607;
    --muted: #9a9a9a;
  }
  * { box-sizing: border-box; margin: 0; padding: 0; }
  html, body { width: 1200px; height: 930px; overflow: hidden; }
  body {
    background: var(--bg);
    font-family: "Roboto", Arial, sans-serif;
    position: relative;
  }
  .card {
    position: absolute;
    left: 230px;
    width: 740px;
    height: 420px;
    border-radius: 22px;
    overflow: hidden;
    box-shadow: 0 6px 18px rgba(0,0,0,.25);
  }
  .card-front { top: 30px; background: var(--card-black); color: var(--paper); }
  .card-back { top: 480px; background: var(--paper); color: var(--ink); }

  .brand { position: absolute; display: flex; align-items: center; gap: 22px; }
  .brand-dot { width: 150px; height: 150px; border-radius: 50%; background: var(--blue); flex: none; }
  .brand-name {
    font-family: "Oxygen", Arial, sans-serif;
    font-weight: 400;
    font-size: 44px;
    line-height: 1.0;
    color: var(--blue);
  }
  .card-back .brand-name { color: var(--ink); }
  .brand-name .llc { font-size: 20px; }

  .card-front .brand { left: 150px; top: 36px; }
  .services {
    position: absolute; left: 40px; right: 40px; top: 222px;
    text-align: center; font-size: 19px; line-height: 1.35;
  }
  .rule { position: absolute; height: 2px; background: var(--blue); }
  .card-front .rule { left: 40px; right: 40px; top: 330px; }
  .callout {
    position: absolute; left: 40px; right: 40px; top: 344px;
    text-align: center; font-size: 19px; line-height: 1.35;
  }

  .card-back .brand { left: 36px; top: 60px; }
  .person { position: absolute; right: 56px; top: 40px; text-align: right; }
  .person-name { color: var(--blue); font-size: 40px; font-weight: 500; letter-spacing: .5px; }
  .person-role { font-size: 20px; margin-top: 2px; }
  .accent-bar { position: absolute; right: 0; top: 40px; width: 30px; height: 70px; background: var(--blue); border-left: 5px solid var(--ink); box-shadow: inset 5px 0 0 var(--paper); }
  .card-back .rule { left: 36px; right: 56px; top: 245px; height: 2px; }
  .address { position: absolute; right: 56px; top: 150px; text-align: right; font-size: 20px; line-height: 1.35; }
  .contact { position: absolute; left: 40px; top: 262px; list-style: none; font-size: 20px; line-height: 1.45; }
  .contact li { display: flex; align-items: center; gap: 12px; }
  .contact svg { width: 16px; height: 16px; fill: var(--blue); flex: none; }
  .wave { position: absolute; left: 0; bottom: 0; width: 740px; height: 150px; }
</style>
</head>
<body>

<section class="card card-front" aria-label="Card front">
  <div class="brand">
    <span class="brand-dot"></span>
    <p class="brand-name">Corvana<br>Tongue<br>Works <span class="llc">LLC</span></p>
  </div>
  <p class="services">
    ESL / ENL Language Classes, Private Lessons, and Online Tutors<br>
    PLEXA Training and Testing<br>
    Translating &amp; Interpreting Services
  </p>
  <div class="rule"></div>
  <p class="callout">
    Contact us about Over-the-Phone Interpreting in over 200 languages<br>
    24/7/365
  </p>
</section>

<section class="card card-back" aria-label="Card back">
  <div class="brand">
    <span class="brand-dot"></span>
    <p class="brand-name">Corvana<br>Tongue<br>Works <span class="llc">LLC</span></p>
  </div>
  <div class="person">
    <p class="person-name">RHODA PELLING</p>
    <p class="person-role">President</p>
  </div>
  <div class="accent-bar"></div>
  <p class="address">482 Garnet Ave., Ste. 219<br>Indianapolis, IN 40917 USA</p>
  <div class="rule"></div>
  <ul class="contact">
    <li><svg viewBox="0 0 16 16"><path d="M4 1l3 3-2 2c1 2 3 4 5 5l2-2 3 3-2 3C7 15 1 9 1 3z"/></svg>(555) 481-3062</li>
    <li><svg viewBox="0 0 16 16"><path d="M1 3h14v10H1z M2 4l6 5 6-5v-0.5H2z" fill-rule="evenodd"/></svg>info@corvanatongue.example</li>
    <li><svg viewBox="0 0 16 16"><path d="M8 1a7 7 0 1 0 0 14A7 7 0 0 0 8 1zm0 1.5c1 1.2 1.6 3 1.7 4.8H6.3C6.4 5.5 7 3.7 8 2.5zM2.6 7.3h2.2c.1-1.7.5-3.2 1.2-4.4a5.6 5.6 0 0 0-3.4 4.4zm0 1.4a5.6 5.6 0 0 0 3.4 4.4c-.7-1.2-1.1-2.7-1.2-4.4zm3.7 0h3.4c-.1 1.8-.7 3.6-1.7 4.8-1-1.2-1.6-3-1.7-4.8zm4.9 0c-.1 1.7-.5 3.2-1.2 4.4a5.6 5.6 0 0 0 3.4-4.4zm0-1.4h2.2A5.6 5.6 0 0 0 10 2.9c.7 1.2 1.1 2.7 1.2 4.4z"/></svg>www.corvanatongue.example</li>
  </ul>
  <svg class="wave" viewBox="0 0 740 150" preserveAspectRatio="none" aria-hidden="true">
    <path d="M0 122 L520 122 C560 122 560 62 610 62 L740 62 L740 150 L0 150 Z" fill="#2394d6"/>
    <path d="M0 112 L510 112 C545 112 548 70 585 66 L592 66 C555 72 552 118 515 118 L0 118 Z" fill="#111213"/>
    <path d="M0 126 L740 126" stroke="#ffffff" stroke-width="3"/>
  </svg>
</section>

</body>
</html>
```